KBT Business Cards

We require business cards for our business. We would like a matte black back to the card, with our logo centred in the middle. The front side of the card is open to design.

Target Market(s)

Clients looking for legal services (professional)

Industry/Entity Type

Legal

Contact Information for Business Card

Doran Kelbrath
Partner
Mobile: 0461 738 524
Email: doran@kbtlaw.co
Website: www.kbtlaw.co
Level 3, 118 Wendmore Street
Sydney NSW 2000

Font styles to use
Other font styles liked:
• Avenir

Colors
f04a50
ffffff
1b1b1b

Requirements
Must have
• Black back with logo included in the centre of the card.
• Our font is Avenir.

```html
<!DOCTYPE html>
<html lang="en">
<head>
<meta charset="utf-8">
<title>KBT Business Cards</title>
<link rel="stylesheet" href="https://fonts.googleapis.com/css2?family=Nunito+Sans:wght@400;600;800&display=swap">
<style>
  :root {
    --page-bg: #d9d9d9;
    --card-black: #1b1b1b;
    --card-white: #f6f7f9;
    --brand-red: #b71f3f;
    --ink: #1b1b1b;
    --ink-soft: #2e2e2e;
    --white: #ffffff;
  }
  * { margin: 0; padding: 0; box-sizing: border-box; }
  html, body {
    width: 1200px; height: 1200px; overflow: hidden;
    background: var(--page-bg);
    font-family: "Nunito Sans", "Avenir", sans-serif;
  }
  .sheet { position: relative; width: 1200px; height: 1200px; }
  .card {
    position: absolute; left: 150px;
    width: 900px; height: 514px;
    box-shadow: 0 10px 28px rgba(0,0,0,0.18);
  }
  /* Back */
  .card-back { top: 48px; background: var(--card-black); }
  .card-back .brand {
    position: absolute; left: 50%; top: 50%;
    transform: translate(-50%, -50%);
    display: flex; align-items: center; gap: 30px;
  }
  .brand-square { width: 96px; height: 96px; flex: none; }
  .card-back .brand-square { background: var(--brand-red); }
  .brand-name {
    font-weight: 800; text-transform: uppercase;
    line-height: 1.02; letter-spacing: 0.01em; white-space: nowrap;
  }
  .card-back .brand-name { color: var(--white); font-size: 40px; }

  /* Front */
  .card-front { top: 628px; background: var(--card-white); overflow: hidden; }
  .front-brand {
    position: absolute; left: 70px; top: 150px;
    display: flex; align-items: center; gap: 24px;
  }
  .card-front .brand-square { width: 84px; height: 84px; background: var(--brand-red); }
  .card-front .brand-name { color: var(--ink); font-size: 30px; }
  .divider {
    position: absolute; left: 440px; top: 128px;
    width: 2px; height: 200px; background: var(--brand-red);
  }
  .contact {
    position: absolute; left: 494px; top: 120px;
    color: var(--ink-soft);
  }
  .contact-name {
    color: var(--brand-red); font-weight: 800; font-size: 36px;
    letter-spacing: 0.01em; line-height: 1.1; white-space: nowrap;
  }
  .contact-role {
    font-size: 22px; font-weight: 600; color: var(--ink);
    margin: 6px 0 18px;
  }
  .contact-list { list-style: none; }
  .contact-list li {
    display: flex; align-items: center; gap: 16px;
    font-size: 21px; line-height: 1.75; letter-spacing: 0.02em;
    white-space: nowrap;
  }
  .contact-list svg { width: 20px; height: 20px; flex: none; }
  .web-domain { color: var(--brand-red); }
  .address-band {
    position: absolute; left: 0; bottom: 0;
    width: 100%; height: 112px; background: var(--brand-red);
    display: flex; align-items: center; justify-content: center;
    color: var(--white); font-size: 23px; font-weight: 600;
    letter-spacing: 0.03em;
  }
</style>
</head>
<body>
<main class="sheet">
  <section class="card card-back" aria-label="Card back">
    <div class="brand">
      <span class="brand-square"></span>
      <p class="brand-name">Kelbrath<br>Bowen<br>Tarrant<br>Legal</p>
    </div>
  </section>

  <section class="card card-front" aria-label="Card front">
    <div class="front-brand">
      <span class="brand-square"></span>
      <p class="brand-name">Kelbrath<br>Bowen<br>Tarrant<br>Legal</p>
    </div>

    <div class="divider"></div>

    <div class="contact">
      <h1 class="contact-name">Doran Kelbrath</h1>
      <p class="contact-role">Partner</p>
      <ul class="contact-list">
        <li>
          <svg viewBox="0 0 24 24" aria-hidden="true"><path fill="#b71f3f" d="M6.6 10.8a15.1 15.1 0 0 0 6.6 6.6l2.2-2.2a1 1 0 0 1 1-.25 11.4 11.4 0 0 0 3.6.57 1 1 0 0 1 1 1V20a1 1 0 0 1-1 1A17 17 0 0 1 3 4a1 1 0 0 1 1-1h3.5a1 1 0 0 1 1 1c0 1.250.2 2.45.57 3.57a1 1 0 0 1-.25 1z"/></svg>
          0461 738 524
        </li>
        <li>
          <svg viewBox="0 0 24 24" aria-hidden="true"><rect x="2.5" y="5" width="19" height="14" rx="1.5" fill="none" stroke="#b71f3f" stroke-width="2.2"/><path d="M3 6l9 7 9-7" fill="none" stroke="#b71f3f" stroke-width="2.2"/></svg>
          doran@kbtlaw.co
        </li>
        <li>
          <svg viewBox="0 0 24 24" aria-hidden="true"><circle cx="12" cy="12" r="9.5" fill="none" stroke="#b71f3f" stroke-width="2.2"/><path d="M2.5 12h19M12 2.5c3 3 3 16 0 19M12 2.5c-3 3-3 16 0 19" fill="none" stroke="#b71f3f" stroke-width="1.8"/></svg>
          <span>www.<span class="web-domain">kbtlaw</span>.co</span>
        </li>
      </ul>
    </div>

    <footer class="address-band">Level 3, 118 Wendmore Street Sydney NSW 2000</footer>
  </section>
</main>
</body>
</html>
```